Bork Ventures, Inc. Website redesign

Revamp the website, it is old and outdated. www.borkventuresinc.example

Target Market(s)

Information Technology Consulting and Staffing

Coding

Coded - Design and coding required

Number of Pages Required

5+ page

Colors

Designer to choose colors to be used in the design.

Requirements
Must have
• Outlined text boxes just like from the Tolvane.example site. A clean look

```html
<!DOCTYPE html>
<html lang="en">
<head>
<meta charset="utf-8">
<title>Bork Ventures, Inc. — Mission Integrity Results</title>
<link rel="stylesheet" href="https://fonts.googleapis.com/css2?family=Montserrat:wght@300;400;500;600;700&family=Open+Sans:wght@400;600;700&display=swap">
<style>
:root{
  --red:#931a2e;
  --red-dark:#6e0f20;
  --red-bright:#b3203a;
  --ink:#1c1c22;
  --ink-soft:#4a4a52;
  --night:#15161c;
  --night-2:#23252f;
  --white:#ffffff;
  --paper:#f3f3f5;
  --line:#d9d9de;
}
*{box-sizing:border-box;margin:0;padding:0}
html,body{width:1200px;height:3768px;overflow:hidden}
body{position:relative;background:var(--white);font-family:"Open Sans",Arial,sans-serif;color:var(--ink)}
.abs{position:absolute}
h1,h2,h3,h4{font-family:"Montserrat",Arial,sans-serif;font-weight:400}

/* header */
.site-header{left:0;top:0;width:1200px;height:58px;z-index:5}
.brand{left:60px;top:0;height:58px;display:flex;align-items:center;background:var(--white);padding:0 18px;gap:12px}
.brand-mark{width:14px;height:14px;background:var(--red)}
.brand-name{font-family:"Montserrat",sans-serif;font-weight:700;font-size:17px;color:var(--red);letter-spacing:.5px;white-space:nowrap}
.brand-tag{left:296px;top:12px;height:34px;border:1px solid var(--white);color:var(--white);font-family:"Montserrat",sans-serif;font-size:13px;padding:0 14px;display:flex;align-items:center;letter-spacing:.5px;white-space:nowrap}
.main-nav{right:60px;top:0;height:58px;display:flex;align-items:center;gap:34px}
.main-nav a{color:var(--white);text-decoration:none;font-family:"Montserrat",sans-serif;font-size:14px;padding:6px 0}
.main-nav a.active{border-bottom:2px solid var(--red-bright)}

/* hero */
.hero{left:0;top:0;width:1200px;height:720px;background:
  radial-gradient(ellipse at 70% 40%,rgba(120,30,50,.35),transparent 60%),
  linear-gradient(160deg,#3a3f4c 0%,#22252e 45%,#1a1b22 100%)}
.hero-title{left:0;top:250px;width:1200px;text-align:center;color:var(--white);font-family:"Montserrat",sans-serif;font-weight:600;font-size:66px;letter-spacing:2px}
.hero-sub{left:0;top:340px;width:1200px;text-align:center;color:var(--white);font-family:"Montserrat",sans-serif;font-weight:400;font-size:38px}
.btn{display:inline-flex;align-items:center;justify-content:center;font-family:"Montserrat",sans-serif;font-size:13px;font-weight:600;letter-spacing:1px;text-decoration:none}
.btn-red{background:var(--red);color:var(--white)}
.btn-outline{border:1px solid var(--white);color:var(--white)}
.hero-btn{left:525px;top:430px;width:150px;height:40px}

/* intro band */
.band-shape{left:0;top:620px;width:1200px;height:410px}
.intro-lead{left:90px;top:730px;color:var(--white);font-family:"Montserrat",sans-serif;font-size:31px;line-height:44px;font-weight:400}
.intro-rule{left:470px;top:735px;width:1px;height:190px;background:rgba(255,255,255,.45)}
.intro-copy{left:510px;top:735px;width:560px;color:var(--white);font-size:14px;line-height:23px}
.intro-btn{left:510px;top:870px;width:150px;height:42px}

/* section titles */
.section-title{left:0;width:1200px;text-align:center;font-family:"Montserrat",sans-serif;font-size:42px;color:var(--ink)}

/* services */
.services-title{top:1080px}
.hex{clip-path:polygon(50% 0,100% 25%,100% 75%,50% 100%,0 75%,0 25%)}
.service{top:1160px;width:240px;text-align:center}
.service .hex{width:220px;height:254px;margin:0 auto}
.service h3{margin-top:18px;font-family:"Montserrat",sans-serif;font-weight:600;font-size:19px;line-height:25px;color:var(--ink)}
.svc-1{left:92px}.svc-1 .hex{background:linear-gradient(150deg,#2a1a22,#7a1a2a 55%,#1a1d28)}
.svc-2{left:352px}.svc-2 .hex{background:linear-gradient(150deg,#c5b8b0,#6d6a70 55%,#3a3c46)}
.svc-3{left:620px}.svc-3 .hex{background:linear-gradient(150deg,#e3d7c8,#b08b6a 55%,#5a4c45)}
.svc-4{left:888px}.svc-4 .hex{background:linear-gradient(150deg,#dfe6ee,#aab6c4 55%,#6a7584)}

/* about */
.about-bg{left:0;top:1540px;width:1200px;height:580px;background:linear-gradient(180deg,#fafafb 0%,#e6e7ea 45%,#f4f4f6 100%)}
.about-title{top:1700px}
.about-copy{left:240px;top:1772px;width:720px;text-align:center;font-size:14px;line-height:23px;color:var(--ink-soft)}
.about-copy p+p{margin-top:14px}
.about-btn{left:525px;top:1960px;width:150px;height:40px}

/* pillars */
.pillars-title{left:0;top:2200px;width:1200px;text-align:center;font-family:"Montserrat",sans-serif;font-weight:500;font-size:28px;line-height:38px;color:var(--ink)}
.pillar-center{left:480px;top:2300px;width:230px;height:266px;background:linear-gradient(150deg,#2b3040,#8a2234 50%,#1c1e27)}
.pillar{width:300px}
.pillar .icon{position:absolute;width:84px;height:96px;background:var(--red);display:flex;align-items:center;justify-content:center}
.pillar h4{font-family:"Montserrat",sans-serif;font-weight:600;font-size:17px;color:var(--red);margin-bottom:6px}
.pillar p{font-size:13px;line-height:20px;color:var(--ink-soft)}
.pillar-left .icon{left:0;top:0}
.pillar-left .text{position:absolute;left:108px;top:6px;width:210px}
.pillar-right .icon{right:0;top:0}
.pillar-right .text{position:absolute;right:108px;top:6px;width:210px;text-align:right}
.p-assess{left:88px;top:2310px;height:100px}
.p-recommend{left:88px;top:2465px;height:100px}
.p-monitor{left:812px;top:2310px;height:100px}
.p-manage{left:812px;top:2465px;height:100px}
.p-implement{left:445px;top:2585px;width:300px;height:200px;text-align:center}
.p-implement .icon{left:108px;top:0}
.p-implement .text{position:absolute;left:40px;top:108px;width:220px}

/* team */
.team-shape{left:0;top:2800px;width:1200px;height:680px}
.team-title{top:2910px;color:var(--white)}
.team-panel{left:40px;top:3010px;width:1120px;height:340px;background:var(--white)}
.member-photo{top:3040px;width:220px;height:280px;background:linear-gradient(160deg,#d6d6da,#8e8e96 60%,#5c5c64)}
.m1-photo{left:80px}
.m2-photo{left:620px}
.member{top:3080px;width:300px}
.m1{left:320px}.m2{left:860px}
.member h3{font-family:"Montserrat",sans-serif;font-weight:600;font-size:22px;color:var(--ink)}
.member .role{font-size:13px;color:var(--ink-soft);margin:4px 0 14px}
.member p{font-size:13px;line-height:20px;color:var(--ink-soft)}
.member p b{color:var(--red);font-weight:700}
.member-social{display:flex;gap:8px;margin-top:20px}
.member-social span{width:20px;height:20px;background:var(--ink)}

/* footer */
.site-footer{left:0;top:3490px;width:1200px;height:278px;background:var(--night)}
.f-col{top:3520px;color:#c9c9cf;font-size:13px;line-height:22px}
.f-col h4{font-family:"Montserrat",sans-serif;font-weight:600;font-size:14px;color:var(--white);letter-spacing:.5px;margin-bottom:12px}
.f-contact{left:80px;width:280px}
.f-contact .row{display:flex;gap:10px;align-items:flex-start;margin-bottom:8px}
.f-contact svg{flex:none;margin-top:4px}
.f-links{left:410px;width:160px}
.f-news{left:620px;width:300px}
.news-form{display:flex;margin-top:16px}
.news-input{width:180px;height:34px;background:var(--white);color:#8a8a92;font-size:12px;display:flex;align-items:center;padding-left:10px}
.news-btn{width:80px;height:34px;background:var(--red);color:var(--white);font-family:"Montserrat",sans-serif;font-size:12px;font-weight:600;display:flex;align-items:center;justify-content:center}
.f-social{left:990px;width:160px}
.f-social li{list-style:none;display:flex;align-items:center;gap:10px}
.f-social li::before{content:"";width:8px;height:8px;border-radius:50%;background:var(--red-bright)}
.f-links ul{list-style:none}
.copyright{left:0;top:3736px;width:1200px;text-align:center;color:#8e8e96;font-size:12px}
.f-rule{left:60px;top:3720px;width:1080px;height:1px;background:#2e3038}
</style>
</head>
<body>

<div class="abs hero" role="img" aria-label="Dark photograph of a hand touching a glowing network interface"></div>

<header class="abs site-header">
  <div class="abs brand"><span class="brand-mark"></span><span class="brand-name">BORK VENTURES</span></div>
  <div class="abs brand-tag">Mission Integrity Results</div>
  <nav class="abs main-nav">
    <a href="#" class="active">Home</a>
    <a href="#">About us</a>
    <a href="#">Services</a>
    <a href="#">Strategy</a>
    <a href="#">IT News</a>
    <a href="#">Contact us</a>
  </nav>
</header>

<h1 class="abs hero-title">BORK VENTURES</h1>
<p class="abs hero-sub">Mission Integrity Results</p>
<a href="#" class="abs btn btn-red hero-btn">READ MORE</a>

<svg class="abs band-shape" width="1200" height="410" viewBox="0 0 1200 410" aria-hidden="true">
  <polygon points="0,20 600,90 1200,20 1200,392 0,380" fill="#931a2e"/>
  <polygon points="0,0 380,60 0,60" fill="#6e0f20" opacity=".6"/>
  <polygon points="1200,0 820,60 1200,60" fill="#6e0f20" opacity=".6"/>
</svg>

<h2 class="abs intro-lead">Bringing<br>Thought Leadership<br>and Quality<br>to Every Project</h2>
<div class="abs intro-rule"></div>
<p class="abs intro-copy">Bork Ventures, Inc. is an 8(a) full-service IT consulting company based in the Washington, DC Metro area. We offer specialized, highly customized technology solutions for our customers located throughout the United States. Learn about our Services now.</p>
<a href="#" class="abs btn btn-outline intro-btn">READ MORE</a>

<h2 class="abs section-title services-title">Our Services</h2>
<div class="abs service svc-1"><div class="hex" role="img" aria-label="Photo of server hardware with red lights"></div><h3>Hardware /<br>Software Sales</h3></div>
<div class="abs service svc-2"><div class="hex" role="img" aria-label="Photo of a professional working at a laptop"></div><h3>Professional<br>Services</h3></div>
<div class="abs service svc-3"><div class="hex" role="img" aria-label="Photo of hands reviewing charts on a desk"></div><h3>Technology<br>Assessment</h3></div>
<div class="abs service svc-4"><div class="hex" role="img" aria-label="Photo of consultants meeting at a table"></div><h3>Technology<br>Consulting</h3></div>

<div class="abs about-bg" role="img" aria-label="Faded photo of an office workspace"></div>
<h2 class="abs section-title about-title">About Us</h2>
<div class="abs about-copy">
  <p>Bork Ventures, Inc. is an 8(a) innovative and rapidly growing full-service IT consulting firm. We provide our clients with cutting-edge technologies and the know-how to apply them to their individual business models.</p>
  <p>For over 20 + years, we have been providing reliable IT solutions to businesses in the Washington, DC Metro area and beyond. Our comprehensive services provide clients with unique technology solutions that are customized to meet the specific demands of their business.</p>
</div>
<a href="#" class="abs btn btn-red about-btn">READ MORE</a>

<h2 class="abs pillars-title">These are the five pillars of our<br>successful IT strategy</h2>
<div class="abs hex pillar-center" role="img" aria-label="Photo of a technology specialist at work"></div>

<div class="abs pillar pillar-left p-assess">
  <div class="icon hex"><svg width="34" height="34" viewBox="0 0 34 34" fill="none" stroke="#fff" stroke-width="2.5"><circle cx="14" cy="14" r="9"/><line x1="21" y1="21" x2="30" y2="30"/></svg></div>
  <div class="text"><h4>Assess</h4><p>Our Lean-specific technology audit and data gathering provides us with...</p></div>
</div>
<div class="abs pillar pillar-left p-recommend">
  <div class="icon hex"><svg width="34" height="34" viewBox="0 0 34 34" fill="none" stroke="#fff" stroke-width="2.5"><rect x="7" y="4" width="20" height="26"/><line x1="11" y1="12" x2="23" y2="12"/><line x1="11" y1="18" x2="23" y2="18"/><line x1="11" y1="24" x2="19" y2="24"/></svg></div>
  <div class="text"><h4>Recommend</h4><p>Our research and analysis is summarized in a proposal for individually designed...</p></div>
</div>
<div class="abs pillar pillar-right p-monitor">
  <div class="icon hex"><svg width="34" height="34" viewBox="0 0 34 34" fill="none" stroke="#fff" stroke-width="2.5"><rect x="4" y="6" width="26" height="17"/><line x1="17" y1="23" x2="17" y2="29"/><line x1="10" y1="29" x2="24" y2="29"/></svg></div>
  <div class="text"><h4>Monitor</h4><p>Ensuring that your technology performs optimally and securely at all times is our job.</p></div>
</div>
<div class="abs pillar pillar-right p-manage">
  <div class="icon hex"><svg width="34" height="34" viewBox="0 0 34 34" fill="none" stroke="#fff" stroke-width="2.5"><circle cx="17" cy="17" r="5"/><circle cx="17" cy="17" r="11" stroke-dasharray="5 3"/></svg></div>
  <div class="text"><h4>Manage</h4><p>Our uniquely designed approach to systems maintenance and support helps</p></div>
</div>
<div class="abs pillar p-implement">
  <div class="icon hex"><svg width="34" height="34" viewBox="0 0 34 34" fill="none" stroke="#fff" stroke-width="2.5"><polyline points="7,18 14,25 27,10"/></svg></div>
  <div class="text"><h4>Implement</h4><p>Bork Ventures, Inc. manages all aspects of the implementation process, including design, procurement...</p></div>
</div>

<svg class="abs team-shape" width="1200" height="680" viewBox="0 0 1200 680" aria-hidden="true">
  <polygon points="0,0 1200,70 1200,680 0,680" fill="#931a2e"/>
  <polygon points="0,0 500,29 0,90" fill="#6e0f20" opacity=".5"/>
</svg>
<h2 class="abs section-title team-title">Our Team</h2>
<div class="abs team-panel"></div>
<div class="abs member-photo m1-photo" role="img" aria-label="Portrait photo of Dario Velt"></div>
<div class="abs member m1">
  <h3>Dario Velt</h3>
  <div class="role">Manager Of The Management</div>
  <p>At vero eos et accusamus et iusto odio dignissimos ducimus qui... <b>Read More</b></p>
  <div class="member-social"><span></span><span></span><span></span><span></span></div>
</div>
<div class="abs member-photo m2-photo" role="img" aria-label="Portrait photo of Mina Holloway"></div>
<div class="abs member m2">
  <h3>Mina Holloway</h3>
  <div class="role">Manager Of The Management</div>
  <p>At vero eos et accusamus et iusto odio dignissimos ducimus qui... <b>Read More</b></p>
  <div class="member-social"><span></span><span></span><span></span><span></span></div>
</div>

<footer class="abs site-footer"></footer>
<div class="abs f-col f-contact">
  <h4>CONTACT US</h4>
  <div class="row"><svg width="12" height="14" viewBox="0 0 12 14"><path d="M6 0a5 5 0 0 1 5 5c0 4-5 9-5 9S1 9 1 5a5 5 0 0 1 5-5z" fill="#b3203a"/><circle cx="6" cy="5" r="2" fill="#15161c"/></svg><span>Bork Ventures, Inc. 1400 Harlow Ridge Rd, Suite 200, Brandport, MD 20900</span></div>
  <div class="row"><svg width="12" height="12" viewBox="0 0 12 12"><path d="M2 0h3l1 3-2 1a7 7 0 0 0 4 4l1-2 3 1v3c0 1-1 2-2 2A11 11 0 0 1 0 2c0-1 1-2 2-2z" fill="#b3203a"/></svg><span>301-555-0142</span></div>
  <div class="row"><svg width="14" height="10" viewBox="0 0 14 10"><rect width="14" height="10" fill="#b3203a"/><polyline points="0,0 7,6 14,0" fill="none" stroke="#15161c" stroke-width="1.5"/></svg><span>info@borkventuresinc.example</span></div>
</div>
<div class="abs f-col f-links">
  <h4>QUICK LINKS</h4>
  <ul><li>Home</li><li>About us</li><li>Services</li><li>Strategy</li><li>IT News</li><li>Contact us</li></ul>
</div>
<div class="abs f-col f-news">
  <h4>NEWSLETTER</h4>
  <p>Excepteur sint occaecat cupidatat non proident, sunt in culpa qui.</p>
  <div class="news-form"><div class="news-input">Enter your email address</div><div class="news-btn">Sign Up</div></div>
</div>
<div class="abs f-col f-social">
  <h4>SOCIAL MEDIA</h4>
  <ul><li>Friendbook</li><li>Chirper</li><li>Searchly Plus</li><li>Viewtube</li></ul>
</div>
<div class="abs f-rule"></div>
<p class="abs copyright">© 2016 The Company Name.All Rights Reserved</p>

</body>
</html>
```